Business Card Design Project - del varosi group

dear Sirs

we need business card design for our group ( DEL Varosi Group ) , i have got the Logo design of our group from pixel harbor in previous , so all need details relating to our group i think available with you, as well as the the chosen logo design

we hope to provide us with business card logo that to be appropaite and satisfactory to us .

thanks

note : logo design of our group is attached .
Updates

Reason: please extend the deadline of my project for additional 15 days because i didn't received appropriate design for our gruop yet . kindly beaware that i have received 77 design till now , supossed to send me 200-250 design at least . thanks

Target Market(s)

contents

name : Kerem EL Nadiri

position : Operation Manager

Industry/Entity Type

Business

Requirements
Must have

• person name

group logo
Nice to have
• logo color matching with back background

```html
<!DOCTYPE html>
<html lang="en">
<head>
<meta charset="utf-8">
<title>Del Varosi Group – Business Card</title>
<link href="https://fonts.googleapis.com/css2?family=Quicksand:wght@400;500;600;700&display=swap" rel="stylesheet">
<style>
  :root {
    --page-bg: #e4e6e9;
    --card-dark: #141619;
    --card-dark-2: #1d2024;
    --brand-blue: #2b6fc4;
    --brand-blue-deep: #1f5aa8;
    --ink-light: #f2f4f7;
    --rule-grey: #8d939b;
    --watermark: #223547;
    --tile-white: #fbfbfd;
  }
  * { box-sizing: border-box; margin: 0; padding: 0; }
  html, body { width: 1067px; height: 1200px; overflow: hidden; }
  body {
    background: var(--page-bg);
    font-family: "Quicksand", sans-serif;
    position: relative;
  }
  .card {
    position: absolute;
    left: 103px;
    width: 860px;
    height: 491px;
    background: linear-gradient(135deg, var(--card-dark-2), var(--card-dark) 60%);
    box-shadow: 0 14px 34px rgba(0,0,0,.28);
    overflow: hidden;
  }
  .card--front { top: 80px; }
  .card--back { top: 629px; }

  .front-watermark {
    position: absolute;
    left: 70px; top: 150px;
    font-size: 96px;
    font-weight: 600;
    color: var(--watermark);
    opacity: .55;
    letter-spacing: 2px;
    white-space: nowrap;
  }
  .person-name {
    position: absolute;
    right: 85px; top: 42px;
    font-size: 50px;
    font-weight: 500;
    color: var(--brand-blue);
  }
  .person-role {
    position: absolute;
    right: 90px; top: 110px;
    font-size: 19px;
    font-weight: 500;
    color: var(--ink-light);
  }
  .divider {
    position: absolute;
    left: 30px; right: 35px; top: 140px;
    height: 2px;
    background: var(--rule-grey);
  }
  .contact-list {
    position: absolute;
    right: 85px; top: 165px;
    list-style: none;
    text-align: right;
    font-size: 24px;
    font-weight: 500;
    line-height: 37px;
    color: var(--ink-light);
  }
  .contact-list .web { color: var(--brand-blue); }
  .brand-band {
    position: absolute;
    left: 42px; right: 28px; top: 355px;
    height: 66px;
    border-radius: 33px;
    background: var(--brand-blue);
  }
  .brand-band span {
    position: absolute;
    left: 390px; right: 0;
    top: 0; line-height: 66px;
    text-align: center;
    font-size: 31px;
    font-weight: 500;
    color: var(--ink-light);
  }
  .logo-backer {
    position: absolute;
    left: 82px; top: 250px;
    width: 210px; height: 210px;
    background: var(--brand-blue-deep);
    transform: rotate(-8deg);
  }
  .logo-tile {
    position: absolute;
    left: 100px; top: 255px;
    width: 210px; height: 210px;
    background: var(--tile-white);
    box-shadow: 2px 3px 8px rgba(0,0,0,.35);
    display: flex;
    align-items: center;
    justify-content: center;
    text-align: center;
  }
  .logo-tile span {
    font-size: 25px;
    font-weight: 700;
    line-height: 1.15;
    color: var(--brand-blue);
  }
  .back-mark {
    position: absolute;
    left: 0; right: 0; top: 160px;
    text-align: center;
    font-size: 100px;
    font-weight: 600;
    line-height: 1.05;
    color: var(--watermark);
    letter-spacing: 2px;
  }
  .back-mark small {
    display: block;
    font-size: 100px;
  }
</style>
</head>
<body>
  <section class="card card--front" aria-label="Business card front">
    <div class="front-watermark" aria-hidden="true">DEL VAROSI</div>
    <h1 class="person-name">Kerem EL Nadiri</h1>
    <p class="person-role">Operation Manager</p>
    <div class="divider"></div>
    <ul class="contact-list">
      <li>Phone: 0123 456 789</li>
      <li>Fax: 0123 456 789</li>
      <li class="web">info@yourdomain.com</li>
      <li class="web">www.yourdomain.com</li>
      <li>PO. Box: City name, etc.</li>
    </ul>
    <div class="brand-band"><span>Del Varosi Group</span></div>
    <div class="logo-backer"></div>
    <div class="logo-tile"><span>DEL VAROSI<br>GROUP</span></div>
  </section>

  <section class="card card--back" aria-label="Business card back">
    <p class="back-mark">DEL VAROSI<small>GROUP</small></p>
  </section>
</body>
</html>
```